1 Dimensional cover for digital product

Please note that if a designer comes in with an original design and other designers try to copy them too closely I will always work with the original designer in order to get the actual look I want.
Therefore it is in the interests of the designers to get their concepts in first.

I am designing some audio products for football (soccer players).

I would like a square version and a 16:9 version of the packaging completed. The square version will be for the Sonvia audio cover and the 16:9 for the thumbnails of videos.

I would like the final images in PSP files as a template that I can change the title and the main image.

I am open to creativity in this project but would like it to be a luxury and premium in what it is portraying.

I have added my logo and also the packaging that I currently use on my sister website which is not aimed at football, soccer.

I've also included an image of one of my models. This would NOT be the product image, but it could be a background image, or you may choose to leave it out altogether.

I've also included an example image as the main product image.

Although I have chosen greyscale I would also like to see products with colour.

The product page is at https://kelvarn.global/collections/all
I add this so that you can chose any one of the titles for this template

Target Market(s)

This is aimed at professional footballers

Industry/Entity Type

Sporting Good

Font styles to use
Serif
Sans Serif

Colors

Designer to choose colors to be used in the design.

Requirements
Must have
• This must look like it is made for an affluent market.
• It may also be simple in its design but I do not wish to be too prescriptive with creativity.
• My typography is Montserrat
Nice to have
• Can include the colors of my logos:
• #5BA9DE
• #272B5F
• Or you can choose to go with greyscale
Should not have
• This is a product for serious athletes so it should look very professional and adult orientated (so not cartoonish its look)

```html
<!DOCTYPE html>
<html lang="en">
<head>
<meta charset="utf-8">
<title>Attacking Vision – Hypnosis Sessions</title>
<link href="https://fonts.googleapis.com/css2?family=Montserrat:wght@400;500;600;800&display=swap" rel="stylesheet">
<style>
  :root{
    --white:#ffffff;
    --sky:#15b6e1;
    --teal:#1896bb;
    --teal-deep:#127595;
    --petrol:#0c3b4d;
    --petrol-strip:#0f4a5f;
    --ring:#1a9fc4;
    --ring-deep:#0e7da0;
    --ink:#262d62;
    --brand:#4a9ad6;
    --gold:#b7aa6b;
  }
  html,body{margin:0;padding:0;overflow:hidden;background:var(--white);}
  .cover{
    position:relative;width:1200px;height:675px;overflow:hidden;
    font-family:"Montserrat",sans-serif;background:var(--white);
  }
  .backdrop{position:absolute;inset:0;width:1200px;height:675px;}
  .brand{
    position:absolute;left:40px;top:38px;width:184px;
    display:flex;flex-direction:column;align-items:center;text-align:center;
  }
  .brand-dot{width:46px;height:46px;border-radius:50%;background:var(--brand);margin-bottom:12px;}
  .brand-name{
    color:var(--brand);font-weight:600;font-size:10.5px;letter-spacing:.2px;
    text-transform:uppercase;white-space:nowrap;line-height:13px;
  }
  .brand-sub{
    display:flex;align-items:center;gap:8px;width:100%;margin-top:3px;
    color:var(--ink);font-weight:500;font-size:13.5px;letter-spacing:.6px;
    text-transform:uppercase;line-height:16px;
  }
  .brand-sub::before,.brand-sub::after{content:"";flex:1;height:1px;background:var(--ink);}
  .eyebrow{
    position:absolute;left:119px;top:228px;margin:0;
    color:var(--ink);font-weight:500;font-size:19px;line-height:24px;
  }
  .title{
    position:absolute;left:30px;top:285px;margin:0;width:672px;
    color:var(--white);font-weight:800;font-size:116px;line-height:98px;
    letter-spacing:-3px;text-transform:uppercase;white-space:nowrap;
    text-shadow:4px 5px 8px rgba(0,0,0,.35);
  }
  .title span{display:block;}
  .title .line-two{text-align:right;}
  .benefit{
    position:absolute;left:140px;top:520px;display:flex;align-items:flex-start;gap:19px;
  }
  .benefit-dot{width:29px;height:29px;border-radius:50%;background:var(--gold);flex:none;}
  .benefit-text{
    margin:0;color:var(--white);font-weight:400;font-size:14px;line-height:17px;
    text-transform:uppercase;letter-spacing:.3px;
  }
</style>
</head>
<body>
<main class="cover">
  <svg class="backdrop" viewBox="0 0 1200 675" xmlns="http://www.w3.org/2000/svg">
    <defs>
      <radialGradient id="athlete-tone" gradientUnits="userSpaceOnUse" cx="925" cy="330" r="330"
                      gradientTransform="translate(925 330) scale(0.75 1.1) translate(-925 -330)">
        <stop offset="0" stop-color="#5e5e5e"/>
        <stop offset="0.4" stop-color="#3a3a3a"/>
        <stop offset="0.75" stop-color="#161616"/>
        <stop offset="1" stop-color="#050505"/>
      </radialGradient>
    </defs>
    <path d="M0 168 C220 140 470 80 700 0 L1200 0 L1200 675 L0 675 Z" fill="var(--teal)"/>
    <path d="M0 198 C240 178 480 120 720 40 L1200 40 L1200 675 L0 675 Z" fill="var(--sky)"/>
    <path d="M0 308 C200 300 420 300 700 318 L1200 318 L1200 675 L0 675 Z" fill="var(--teal)"/>
    <path d="M0 360 C200 356 420 362 700 380 L1200 380 L1200 675 L0 675 Z" fill="var(--teal-deep)"/>
    <path d="M0 406 C220 420 440 445 700 470 L1200 470 L1200 675 L0 675 Z" fill="var(--petrol)"/>
    <rect x="0" y="633" width="1200" height="42" fill="var(--petrol-strip)"/>
    <path d="M0 0 L690 0 C480 80 240 150 0 170 Z" fill="var(--white)"/>
    <path d="M682 0 C615 100 584 230 586 340 C588 470 618 580 652 675 L1200 675 L1200 0 Z" fill="var(--ring)"/>
    <path d="M700 0 C638 100 604 230 605 340 C607 470 642 580 690 675 L1200 675 L1200 0 Z" fill="var(--ring-deep)"/>
    <path d="M710 0 C646 100 612 230 613 340 C615 470 652 580 719 675 L1200 675 L1200 0 Z"
          fill="url(#athlete-tone)" role="img"
          aria-label="Black and white photo of a footballer in a training top, leaning forward with hands clasped, against a dark starry backdrop"/>
  </svg>

  <div class="brand">
    <span class="brand-dot"></span>
    <span class="brand-name">Elias Varne Hypnotherapy</span>
    <span class="brand-sub">Kelvarn</span>
  </div>

  <p class="eyebrow">Hypnosis sessions</p>

  <h1 class="title"><span class="line-one">Attacking</span><span class="line-two">Vision</span></h1>

  <div class="benefit">
    <span class="benefit-dot"></span>
    <p class="benefit-text">Improve your decision making<br>when you are attacking.</p>
  </div>
</main>
</body>
</html>
```